business card for a massage therapy practice named 'Cedar and Willow Massage Studio'

I really need a trendy, yet easy on the eyes business card to complement my logo. Ideally with some gold or rose gold foil work.

My uploaded file of the logo I have in horizontal but I have a vertical version as well. Another color that is used in the website is a blush pink here and there. I'd like to see some trendy tropical leaves in the design.

```html
<!DOCTYPE html>
<html lang="en">
<head>
<meta charset="utf-8">
<title>Cedar and Willow Massage Studio – Business Card</title>
<link rel="stylesheet" href="https://fonts.googleapis.com/css2?family=Amatic+SC:wght@700&family=Questrial&display=swap">
<style>
  :root {
    --backdrop: #a4a4a4;
    --card-front: #f7f8fa;
    --card-back: #ffffff;
    --gold: #9b8457;
    --ink: #1c1c1c;
    --text-grey: #5a5a5a;
    --leaf: #6a9e3c;
    --leaf-soft: rgba(106, 158, 60, 0);
  }
  * { box-sizing: border-box; margin: 0; padding: 0; }
  html, body {
    width: 1200px; height: 1200px; overflow: hidden;
    background: var(--backdrop);
  }
  .canvas { position: relative; width: 1200px; height: 1200px; }
  .card {
    position: absolute; left: 246px; width: 681px; height: 391px;
    overflow: hidden;
  }
  .card--front { top: 171px; background: var(--card-front); }
  .card--back { top: 654px; background: var(--card-back); }

  .leaves { position: absolute; }
  .leaves--top-right {
    right: 0; top: 0; width: 132px; height: 146px;
    background: radial-gradient(ellipse at 100% 0%, var(--leaf) 0%, rgba(106,158,60,.75) 45%, var(--leaf-soft) 75%);
  }
  .leaves--bottom-left {
    left: 0; bottom: 0; width: 124px; height: 128px;
    background: radial-gradient(ellipse at 0% 100%, var(--leaf) 0%, rgba(106,158,60,.75) 45%, var(--leaf-soft) 75%);
  }

  .brand {
    position: absolute; display: flex; align-items: center;
    font-family: "Questrial", sans-serif; color: var(--ink);
  }
  .brand__dot { flex: none; border-radius: 50%; background: var(--gold); }
  .brand__name { line-height: 1.15; }

  .card--front .brand { left: 64px; top: 112px; gap: 16px; }
  .card--front .brand__dot { width: 30px; height: 30px; }
  .card--front .brand__name { font-size: 27px; }

  .card--back .brand { left: 0; right: 0; top: 142px; justify-content: center; gap: 22px; }
  .card--back .brand__dot { width: 44px; height: 44px; }
  .card--back .brand__name { font-size: 40px; }

  .contact { position: absolute; left: 386px; top: 117px; font-family: "Questrial", sans-serif; }
  .contact__name {
    font-family: "Amatic SC", sans-serif; font-weight: 700;
    font-size: 36px; color: var(--gold); letter-spacing: 1px; line-height: 1;
  }
  .contact__role {
    margin-top: 6px; font-size: 17px; color: var(--text-grey); letter-spacing: 2px;
  }
  .contact__list { list-style: none; margin-top: 48px; }
  .contact__list li {
    font-size: 17px; color: var(--text-grey); letter-spacing: .6px;
    line-height: 32px;
  }

  .website {
    position: absolute; left: 0; right: 0; top: 324px; text-align: center;
    font-family: "Questrial", sans-serif; font-weight: 700;
    font-size: 17px; color: var(--gold); letter-spacing: 1px;
  }
</style>
</head>
<body>
<main class="canvas">
  <section class="card card--front">
    <div class="leaves leaves--top-right" role="img" aria-label="Tropical palm leaves in the corner"></div>
    <div class="leaves leaves--bottom-left" role="img" aria-label="Tropical palm leaf in the corner"></div>
    <div class="brand">
      <span class="brand__dot"></span>
      <span class="brand__name">Cedar and Willow<br>Massage Studio</span>
    </div>
    <div class="contact">
      <h1 class="contact__name">MARA QUINN</h1>
      <p class="contact__role">Artist</p>
      <ul class="contact__list">
        <li>Phone: +123 555 014 7</li>
        <li>Email: hello@cedarwillow.com</li>
        <li>Web: www.cedarwillow.com</li>
      </ul>
    </div>
  </section>

  <section class="card card--back">
    <div class="brand">
      <span class="brand__dot"></span>
      <span class="brand__name">Cedar and Willow<br>Massage Studio</span>
    </div>
    <p class="website">www.cedarwillow.com</p>
  </section>
</main>
</body>
</html>
```